Velmora Freightway Solutions Business cards

Would like a very unique design catchy but professional for business cards. Please use log provided.Marlon WellsCeo and Founder TransCon Logistix Solutions1-888-913-3225mwells@tlsolutionsus.comwww.tlsolutionsus.com

```html
<!DOCTYPE html>
<html lang="en">
<head>
<meta charset="utf-8">
<title>Velmora Freightway Solutions – Business Cards</title>
<link rel="stylesheet" href="https://fonts.googleapis.com/css2?family=Lato:wght@400;700&display=swap">
<style>
  :root {
    --backdrop: #2b2b2d;
    --card: #111112;
    --card-edge: #1a1a1b;
    --brand-blue: #1670c4;
    --accent-red: #ee1c25;
    --text-light: #e6e6e6;
    --divider: #8a8a8a;
  }
  * { margin: 0; padding: 0; box-sizing: border-box; }
  html, body {
    width: 1200px; height: 900px; overflow: hidden;
    background: var(--backdrop);
    font-family: "Lato", sans-serif;
  }
  .stage { position: relative; width: 1200px; height: 900px; }
  .card {
    position: absolute; left: 320px;
    width: 560px; height: 320px;
    background: linear-gradient(160deg, var(--card-edge), var(--card));
    box-shadow: 0 14px 30px rgba(0,0,0,.45);
    overflow: hidden;
  }
  .card::after {
    content: ""; position: absolute; left: 0; right: 0; bottom: 0;
    height: 10px; background: var(--accent-red);
  }
  .card--front { top: 110px; }
  .card--back { top: 470px; }

  .brand {
    position: absolute; inset: 0 0 10px 0;
    display: flex; align-items: center; justify-content: center; gap: 12px;
  }
  .brand__mark { width: 18px; height: 18px; background: var(--accent-red); }
  .brand__name {
    color: var(--brand-blue); font-weight: 700;
    font-size: 24px; letter-spacing: 1.5px; text-transform: uppercase;
  }

  .holder {
    position: absolute; left: 40px; top: 130px; width: 235px; text-align: right;
  }
  .holder__name {
    color: var(--brand-blue); font-weight: 700; font-size: 20px;
    letter-spacing: 1.5px; text-transform: uppercase;
  }
  .holder__title { color: var(--text-light); font-size: 14px; margin-top: 2px; }

  .divider {
    position: absolute; left: 300px; top: 118px;
    width: 1px; height: 72px; background: var(--divider);
  }
  .contacts {
    position: absolute; left: 322px; top: 118px; list-style: none;
    color: var(--text-light); font-size: 15px;
  }
  .contacts li { display: flex; align-items: center; gap: 8px; height: 24px; }
  .contacts svg { width: 12px; height: 12px; fill: var(--brand-blue); flex: none; }
</style>
</head>
<body>
<main class="stage">
  <section class="card card--front" aria-label="Card front">
    <div class="brand">
      <span class="brand__mark"></span>
      <span class="brand__name">Velmora Freightway Solutions</span>
    </div>
  </section>

  <section class="card card--back" aria-label="Card back">
    <div class="holder">
      <p class="holder__name">Dorian Pike</p>
      <p class="holder__title">CEO and Founder</p>
    </div>
    <span class="divider"></span>
    <ul class="contacts">
      <li>
        <svg viewBox="0 0 12 12" aria-hidden="true"><path d="M2.5 0.5l2 2.5-1.2 1.2c.7 1.5 2 2.8 3.5 3.5L8 6.5l2.5 2-1 2.5C5 10.5 1.5 7 .5 2.5z"/></svg>
        1-888-470-6158
      </li>
      <li>
        <svg viewBox="0 0 12 12" aria-hidden="true"><path d="M0 2h12v8H0z M1 3l5 3.5L11 3v-.2H1z" fill-rule="evenodd"/></svg>
        dpike@vfwayroutes.com
      </li>
      <li>
        <svg viewBox="0 0 12 12" aria-hidden="true"><circle cx="6" cy="6" r="6"/><path d="M1 6h10M6 0.5c-2 2.5-2 8.5 0 11M6 0.5c2 2.5 2 8.5 0 11" stroke="#111112" stroke-width=".8" fill="none"/></svg>
        www.vfwayroutes.com
      </li>
    </ul>
  </section>
</main>
</body>
</html>
```